Business Card Design Project for Heron Lending

Hello there,

We are looking for a business card design for our new Heron Lending car financing company. We are looking for a business card that will include:

- An address
- Telephone number and extension
- Employee Name
- Employee Title
- Our logo and name clearly visible

We are including our logo with this writeup, we are looking to convey friendliness, trus and memorability. Colors and everything else is up to you.

Target Market(s)

18-34 year old males and females

Industry/Entity Type

Business

```html
<!DOCTYPE html>
<html lang="en">
<head>
<meta charset="utf-8">
<title>Heron Lending – Business Card</title>
<link rel="stylesheet" href="https://fonts.googleapis.com/css2?family=Open+Sans:wght@400;600;700&display=swap">
<style>
  :root {
    --backdrop: #e9eaeb;
    --card-paper: #f1f1f0;
    --brand-navy: #0e3a52;
    --brand-charcoal: #1f1c1b;
    --text-on-navy: #e8eef2;
  }
  * { box-sizing: border-box; margin: 0; padding: 0; }
  html, body {
    width: 1200px;
    height: 675px;
    overflow: hidden;
    background: var(--backdrop);
    font-family: "Open Sans", Arial, sans-serif;
  }
  .card {
    position: absolute;
    left: 100px;
    top: 51px;
    width: 1000px;
    height: 572px;
    background: var(--card-paper);
    overflow: hidden;
    box-shadow: 0 10px 30px rgba(0,0,0,0.12);
  }
  .card-bands {
    position: absolute;
    left: 0;
    bottom: 0;
    width: 1000px;
    height: 218px;
  }
  .band-navy { fill: var(--brand-navy); }
  .band-charcoal { fill: var(--brand-charcoal); }

  .brand-name {
    position: absolute;
    left: 560px;
    top: 150px;
    width: 360px;
    text-align: center;
    font-size: 46px;
    font-weight: 600;
    letter-spacing: 2px;
    color: var(--brand-navy);
  }

  .person {
    position: absolute;
    left: 64px;
    top: 262px;
    color: var(--brand-navy);
  }
  .person-name {
    font-size: 30px;
    font-weight: 700;
    line-height: 1.2;
  }
  .person-title {
    font-size: 22px;
    font-weight: 400;
    padding-left: 16px;
    line-height: 1.3;
  }

  .contact {
    position: absolute;
    left: 64px;
    bottom: 52px;
    list-style: none;
    color: var(--text-on-navy);
    font-size: 21px;
    line-height: 1.45;
  }
  .contact-item {
    display: flex;
    align-items: center;
    gap: 12px;
  }
  .contact-icon {
    width: 18px;
    height: 18px;
    fill: var(--text-on-navy);
    flex: none;
  }
</style>
</head>
<body>
  <main class="card" aria-label="Heron Lending business card">
    <svg class="card-bands" viewBox="0 0 1000 218" aria-hidden="true">
      <polygon class="band-charcoal" points="650,0 1000,0 1000,218 720,218"/>
      <polygon class="band-navy" points="0,0 650,0 720,218 0,218"/>
    </svg>

    <div class="brand-name">Heron Lending</div>

    <section class="person">
      <h1 class="person-name">Your Long Name</h1>
      <p class="person-title">Your Title</p>
    </section>

    <ul class="contact">
      <li class="contact-item">
        <svg class="contact-icon" viewBox="0 0 24 24" aria-hidden="true">
          <path d="M6.6 10.8a15.1 15.1 0 0 0 6.6 6.6l2.2-2.2a1 1 0 0 1 1-.25 11.4 11.4 0 0 0 3.6.57 1 1 0 0 1 1 1V20a1 1 0 0 1-1 1A17 17 0 0 1 3 4a1 1 0 0 1 1-1h3.5a1 1 0 0 1 1 1c0 1.25.2 2.45.57 3.57a1 1 0 0 1-.25 1z"/>
        </svg>
        <span>00.00.00.0000</span>
      </li>
      <li class="contact-item">
        <svg class="contact-icon" viewBox="0 0 24 24" aria-hidden="true">
          <path d="M12 2a7 7 0 0 0-7 7c0 5.25 7 13 7 13s7-7.75 7-13a7 7 0 0 0-7-7zm0 9.5A2.5 2.5 0 1 1 12 6.5a2.5 2.5 0 0 1 0 5z"/>
        </svg>
        <span>Your Commercial or office address</span>
      </li>
    </ul>
  </main>
</body>
</html>
```